Home Remodeling company needs a business card design

we need a business card design for home remodeling company in hamilton county, indiana USA. we offers a wide range of construction services including whole house renovations, Design and Build Basements and Kitchen and Bathroom Remodeling . we would like to see designs for both site of business card that use the same color of the company logo and also including all information below :
1- Karim Feltous CEO / General Contractor
2- all company contacts Telephone numbers ( 1-888-DULOM-47 ) ( 317-555-0193) email address ( info@dulomhome.com) website ( www.dulomhome.com ) and social media logos (Facebook- twitter- google plus )
3- company logo
4- licensed . insured . bonded

```html
<!DOCTYPE html>
<html lang="en">
<head>
<meta charset="utf-8">
<title>Dulom Home Remodeling – Business Card</title>
<link rel="stylesheet" href="https://fonts.googleapis.com/css2?family=Arimo:wght@400;700&display=swap">
<style>
  :root {
    --page: #e9e6e1;
    --red-dark: #c42a3b;
    --red-light: #e24d5e;
    --charcoal: #3a3b3e;
    --charcoal-deep: #2b2c2f;
    --white: #ffffff;
    --ink-grey: #4a4b4f;
    --card-w: 540px;
    --card-h: 309px;
  }
  * { box-sizing: border-box; margin: 0; padding: 0; }
  html, body { width: 1200px; height: 892px; overflow: hidden; }
  body {
    background: var(--page);
    font-family: "Arimo", Arial, sans-serif;
    position: relative;
  }
  .card {
    position: absolute;
    top: 291px;
    width: var(--card-w);
    height: var(--card-h);
    overflow: hidden;
    box-shadow: 0 6px 18px rgba(0,0,0,.22);
  }
  .card--front { left: 40px; background: linear-gradient(135deg, var(--red-dark) 0%, var(--red-light) 55%, var(--red-dark) 100%); }
  .card--back { left: 620px; background: linear-gradient(135deg, var(--charcoal) 0%, var(--charcoal-deep) 100%); }

  .bottom-band {
    position: absolute; left: 0; right: 0; bottom: 0; height: 44px;
    border-top: 4px solid var(--white);
  }
  .card--front .bottom-band { background: var(--charcoal); }
  .card--back .bottom-band { background: var(--red-dark); }

  /* front */
  .brand {
    position: absolute; left: 30px; top: 96px; width: 230px;
    white-space: nowrap;
  }
  .brand__name {
    font-weight: 700; font-size: 50px; letter-spacing: 1px;
    color: var(--ink-grey); line-height: 1;
  }
  .brand__tagline {
    margin-top: 8px;
    font-size: 12px; letter-spacing: 5.4px; color: var(--ink-grey);
  }
  .brand__credentials {
    margin-top: 6px;
    font-size: 12px; letter-spacing: .6px; color: var(--ink-grey);
  }
  .divider {
    position: absolute; left: 275px; top: 24px; width: 1px; height: 208px;
    background: rgba(255,255,255,.75);
  }
  .contact { position: absolute; left: 295px; top: 38px; width: 230px; white-space: nowrap; }
  .contact__name { font-weight: 700; font-size: 26px; color: var(--white); }
  .contact__title { font-size: 15px; color: var(--ink-grey); margin-top: 3px; }
  .contact__list { list-style: none; margin-top: 18px; }
  .contact__item {
    display: flex; align-items: center; gap: 8px;
    font-size: 14.5px; color: var(--white); line-height: 23px;
  }
  .contact__icon { width: 13px; height: 13px; flex: none; }
  .social { display: flex; gap: 8px; margin-top: 14px; }
  .social__badge { width: 16px; height: 16px; background: var(--ink-grey); border-radius: 2px; }

  /* back */
  .back-brand {
    position: absolute; left: 0; right: 0; top: 78px; text-align: center;
  }
  .back-brand__name {
    font-weight: 700; font-size: 78px; letter-spacing: 2px;
    color: var(--white); line-height: 1;
  }
  .back-brand__tagline {
    margin-top: 12px; font-size: 18px; letter-spacing: 10px; color: var(--white);
    padding-left: 10px;
  }
</style>
</head>
<body>

<section class="card card--front" aria-label="Business card front">
  <div class="brand">
    <div class="brand__name">DULOM</div>
    <div class="brand__tagline">HOME REMODELING</div>
    <div class="brand__credentials">LICENSED . INSURED . BONDED</div>
  </div>

  <div class="divider"></div>

  <div class="contact">
    <div class="contact__name">Karim Feltous</div>
    <div class="contact__title">CEO / General Contractor</div>
    <ul class="contact__list">
      <li class="contact__item">
        <svg class="contact__icon" viewBox="0 0 16 16"><path fill="#fff" d="M3 1l3 3-1.5 2c1 2 3 4 5 5L11.5 9.5l3 3L12 15C6 14 2 10 1 4z"/></svg>
        1-888-DULOM-47
      </li>
      <li class="contact__item">
        <svg class="contact__icon" viewBox="0 0 16 16"><rect x="4" y="1" width="8" height="14" rx="1.5" fill="#fff"/><rect x="5.5" y="3" width="5" height="8" fill="#c42a3b"/></svg>
        317-555-0193
      </li>
      <li class="contact__item">
        <svg class="contact__icon" viewBox="0 0 16 16"><rect x="1" y="3" width="14" height="10" fill="#fff"/><path d="M1 3l7 6 7-6" fill="none" stroke="#c42a3b" stroke-width="1.4"/></svg>
        info@dulomhome.com
      </li>
      <li class="contact__item">
        <svg class="contact__icon" viewBox="0 0 16 16"><circle cx="8" cy="8" r="6.5" fill="none" stroke="#fff" stroke-width="1.5"/><path d="M1.5 8h13M8 1.5c-3 3.5-3 9.5 0 13M8 1.5c3 3.5 3 9.5 0 13" fill="none" stroke="#fff" stroke-width="1.1"/></svg>
        www.dulomhome.com
      </li>
    </ul>
    <div class="social" aria-label="Social media">
      <span class="social__badge"></span>
      <span class="social__badge"></span>
      <span class="social__badge"></span>
    </div>
  </div>

  <div class="bottom-band"></div>
</section>

<section class="card card--back" aria-label="Business card back">
  <div class="back-brand">
    <div class="back-brand__name">DULOM</div>
    <div class="back-brand__tagline">HOME REMODELING</div>
  </div>
  <div class="bottom-band"></div>
</section>

</body>
</html>
```